Web Design Project for a beach town business owner who supports new families with their babies.

I'm looking for a basic website with the following pages: home, about, services, FAQs, blog, and contact page. I have images and content ready to go.

Target Market(s)

Men and women between the ages of 22 and 42, growing families

Industry/Entity Type

Postpartum Doula

Coding

Number of Pages Required

Font styles to use
Serif
Other font styles liked:
• My logo font is "Nexa Bold" - so coordinating fonts with that are ideal

Colors
00AB8E
00BBA5
67D7C9
C6EFE9
E9F9F6
EE7325
F08F49
F5BC92
FAE3D3
FDF4ED

Requirements
Must have
• Warm and professional vibe, multicultural images, aligned with my branding colors and font ("Nexa Bold"; COLORS: light blue hex: #2FCEC2 R: 47 G: 206 B: 194 dark blue hex: #007C7C R: 0 G: 124 B: 124 orange hex: #F77B4E R: 247 G: 123 B: 78), good SEO
Should not have
• Ultra feminine images, baby bottles, cutesy images.

```html
<!DOCTYPE html>
<html lang="en">
<head>
<meta charset="utf-8">
<title>Tidewell Families Postpartum Care</title>
<link href="https://fonts.googleapis.com/css2?family=Montserrat:wght@500;600;700;800&family=Karla:wght@400;700&family=Dancing+Script:wght@500&display=swap" rel="stylesheet">
<style>
:root{
  --teal-dark:#137070;
  --teal:#2ec4b6;
  --teal-deep:#0f6b6b;
  --orange:#f26a3e;
  --ink:#1f1f1f;
  --body:#333;
  --white:#fff;
  --footer:#222222;
  --fb:#2b4ba3;
  --tw:#1d9bf0;
  --li:#1b1a4f;
}
*{box-sizing:border-box;margin:0;padding:0}
html,body{width:1200px;height:2344px;overflow:hidden}
body{position:relative;background:var(--white);font-family:"Karla",sans-serif;color:var(--body)}
.abs{position:absolute}
/* header */
.site-header{position:absolute;left:0;top:0;width:1200px;height:80px;background:var(--white);z-index:3}
.brand-badge{position:absolute;left:128px;top:2px;width:132px;height:132px;border-radius:50%;background:var(--white);z-index:4;display:flex;align-items:center;justify-content:center;text-align:center;font-family:"Montserrat",sans-serif;font-weight:700;font-size:15px;line-height:1.2;color:var(--teal)}
.main-nav a,.footer-nav a{position:absolute;font-family:"Montserrat",sans-serif;font-weight:600;font-size:14px;color:var(--ink);text-decoration:none;white-space:nowrap}
.main-nav a{top:31px}
.main-nav a.active{color:var(--orange)}
.main-nav a.active::after{content:"";position:absolute;left:0;right:0;bottom:-5px;height:3px;background:var(--orange)}
.social{position:absolute;width:29px;height:29px;border-radius:50%}
.social.fb{background:var(--fb)}.social.tw{background:var(--tw)}.social.li{background:var(--li)}
/* hero */
.hero{position:absolute;left:0;top:80px;width:1200px;height:620px;background:radial-gradient(ellipse at 72% 45%,#c99a86 0 18%,transparent 34%),linear-gradient(100deg,#3c5a2a 0%,#5f7d3d 35%,#4d6b34 55%,#2a8ac4 80%,#1e86c2 100%)}
.hero-title{position:absolute;left:131px;top:150px;font-family:"Montserrat",sans-serif;font-weight:800;font-size:48px;line-height:53px;color:var(--white)}
.btn{position:absolute;display:flex;align-items:center;justify-content:center;font-family:"Montserrat",sans-serif;font-weight:800;color:var(--white);border-radius:5px;text-decoration:none}
.btn-read{left:135px;top:390px;width:174px;height:55px;font-size:16px;background:var(--teal);box-shadow:0 4px 8px rgba(0,0,0,.3)}
.dots{position:absolute;left:563px;top:577px;display:flex;gap:9px;align-items:center}
.dots span{width:7px;height:7px;border-radius:50%;background:var(--white)}
.dots span.on{width:11px;height:11px;background:var(--orange);border:2px solid var(--white)}
/* welcome */
.welcome{position:absolute;left:0;top:700px;width:1200px;height:587px;background:var(--teal-dark)}
.welcome-art{position:absolute;left:78px;top:76px}
.welcome-text{position:absolute;left:650px;top:57px;width:480px;color:var(--white)}
.eyebrow{font-family:"Montserrat",sans-serif;font-weight:700;font-size:15px;letter-spacing:.3px}
.welcome h2{font-family:"Montserrat",sans-serif;font-weight:800;font-size:29px;margin-top:4px}
.welcome .script{font-family:"Dancing Script",cursive;font-size:27px;line-height:31px;margin-top:14px}
.welcome p{font-size:14.2px;line-height:21px;margin-top:20px}
.welcome p.first{margin-top:30px}
/* support */
.support-intro{position:absolute;left:132px;top:1340px;width:430px;font-size:18.5px;line-height:26px;color:var(--ink);font-weight:400}
.support-list{position:absolute;left:134px;top:1455px;width:440px;list-style:none}
.support-list li{position:relative;padding-left:32px;font-size:14.3px;line-height:21px;margin-bottom:24px;color:var(--ink)}
.support-list li::before{content:"";position:absolute;left:0;top:5px;width:16px;height:16px;border-radius:50%;background:var(--orange)}
.support-list strong{color:var(--teal-deep);font-weight:700}
.portrait{position:absolute;left:619px;top:1337px;width:422px;height:422px;border-radius:50%;border:1.5px solid var(--teal);display:flex;align-items:center;justify-content:center}
.portrait div{width:404px;height:404px;border-radius:50%;background:linear-gradient(160deg,#8a4a3a 0%,#b06c58 30%,#d9b7a6 55%,#2a2228 75%,#f0d3de 100%)}
.support-outro{position:absolute;left:132px;top:1798px;width:870px;font-size:14.3px;line-height:21px;color:var(--ink)}
.support-outro p+p{margin-top:20px}
/* cta */
.cta-band{position:absolute;left:0;top:1964px;width:1200px;height:112px;background:radial-gradient(ellipse at 20% 30%,#2a9a9a 0,transparent 50%),linear-gradient(90deg,#1b7f84,#1f8f92 50%,#187a80)}
.btn-start{left:466px;top:26px;width:267px;height:63px;font-size:19px;background:var(--orange)}
/* footer */
.site-footer{position:absolute;left:0;top:2076px;width:1200px;height:268px;background:var(--footer);color:var(--white)}
.footer-badge{position:absolute;left:133px;top:41px;width:188px;height:188px;border-radius:50%;background:var(--white);display:flex;align-items:center;justify-content:center;text-align:center;font-family:"Montserrat",sans-serif;font-weight:700;font-size:20px;line-height:1.25;color:var(--teal)}
.follow{position:absolute;left:875px;top:53px;font-family:"Montserrat",sans-serif;font-weight:500;font-size:12.5px;letter-spacing:.5px}
.rule{position:absolute;left:541px;width:528px;height:1px;background:#bbb}
.footer-nav a{top:131px;color:var(--white);font-weight:500;font-size:14.5px}
.copyright{position:absolute;right:133px;top:208px;font-size:13.5px}
</style>
</head>
<body>
<header class="site-header">
  <nav class="main-nav">
    <a class="active" style="left:405px" href="#">HOME</a>
    <a style="left:488px" href="#">ABOUT</a>
    <a style="left:582px" href="#">SERVICES</a>
    <a style="left:695px" href="#">FAQS</a>
    <a style="left:779px" href="#">BLOG</a>
    <a style="left:861px" href="#">CONTACT</a>
  </nav>
  <span class="social fb" style="left:966px;top:25px"></span>
  <span class="social tw" style="left:1003px;top:25px"></span>
  <span class="social li" style="left:1040px;top:25px"></span>
</header>
<div class="brand-badge">Tidewell<br>Families</div>

<section class="hero" role="img" aria-label="Smiling postpartum doula in a blue blouse outdoors against a green garden background">
  <h1 class="hero-title">TIDEWELL<br>FAMILIES<br>POSTPARTUM<br>CARE</h1>
  <a class="btn btn-read" href="#">READ MORE</a>
  <div class="dots"><span></span><span></span><span class="on"></span><span></span><span></span></div>
</section>

<section class="welcome">
  <svg class="welcome-art" width="535" height="447" viewBox="0 0 535 447" role="img" aria-label="Family of three smiling together under a tree in a park">
    <defs>
      <linearGradient id="parkTones" x1="0" y1="0" x2="1" y2="1">
        <stop offset="0" stop-color="#8fbf4a"/>
        <stop offset="0.45" stop-color="#7a5a46"/>
        <stop offset="0.75" stop-color="#c7b8c4"/>
        <stop offset="1" stop-color="#a9c64e"/>
      </linearGradient>
    </defs>
    <path fill="url(#parkTones)" d="M40 40 C80 5 170 10 200 60 C240 90 300 60 380 70 C470 80 540 130 532 210 C525 280 460 290 420 330 C380 380 350 440 270 445 C200 450 170 390 100 400 C40 410 5 390 10 330 C15 270 30 230 25 170 C20 110 10 70 40 40 Z"/>
  </svg>
  <div class="welcome-text">
    <div class="eyebrow">WELCOME TO</div>
    <h2>TIDEWELL FAMILIES.</h2>
    <div class="script">Congratulations on your birth and welcome to Tidewell Families Postpartum Care!</div>
    <p class="first">Hi, I’m Dana Reyes, a certified postpartum care expert and educator serving families of all varieties in the greater San Diego area and beyond.</p>
    <p>My passion as a professional is showing new parents just like you that whether you’ve just had your first child or your fifth, you cannot only survive your postpartum period (also known as the 4th trimester), but you and your family can THRIVE – with the kind of compassionate, skilled, and targeted support for your unique needs that only an expert can provide. That’s where I come in.</p>
    <p>Did you know that, on average, new parents won’t see their midwife or obstetrician until 6 weeks after giving birth to their baby(ies)? Working with a postpartum care expert (also known as a doula) can help fill in this gap in continuity of care by providing individualized support for parents and families as they transition to life with their new baby.</p>
  </div>
</section>

<h3 class="support-intro">My work includes four key areas of support that are designed to positively impact your postpartum period with your baby:</h3>
<ul class="support-list">
  <li>I enhance <strong>bonding and attachment</strong> between parents(s) and baby in the areas of feeding, soothing, learning baby’s cues, babywearing, and playing with baby.</li>
  <li>I provide <strong>practical, evidence-based information</strong> about baby care and help identify what is normal and what is outside the range of normal for parent(s) and baby.</li>
  <li>I prioritize the <strong>mental and emotional health</strong> of parent(s) and help identify potential warning signs that indicate that medical care may be needed.</li>
  <li>I offer <strong>hands-on support</strong> with baby(ies), older siblings, pets, and light home upkeep and meal preparation.</li>
</ul>
<div class="portrait"><div role="img" aria-label="Doula holding a newborn baby in front of a brick fireplace"></div></div>
<div class="support-outro">
  <p>Families who work with me report feeling more connected, happy, and informed than their parenting-veteran friends and family members – both during the time that I work with them and beyond.</p>
  <p>Struggle is a normal part of growth and learning. Your postpartum period is a time for healing and recovering from birth, bonding with your baby, and establishing a healthy feeding relationship in whatever way works best for your family. Let me show you how to remove the struggle from this magical time!</p>
</div>

<section class="cta-band">
  <a class="btn btn-start" href="#">LET’S GET STARTED</a>
</section>

<footer class="site-footer">
  <div class="footer-badge">Tidewell<br>Families</div>
  <div class="follow">FOLLOW</div>
  <span class="social fb" style="left:959px;top:46px;width:31px;height:31px"></span>
  <span class="social tw" style="left:998px;top:46px;width:31px;height:31px"></span>
  <span class="social li" style="left:1037px;top:46px;width:31px;height:31px"></span>
  <div class="rule" style="top:109px"></div>
  <nav class="footer-nav">
    <a style="left:544px" href="#">HOME</a>
    <a style="left:627px" href="#">ABOUT</a>
    <a style="left:720px" href="#">SERVICES</a>
    <a style="left:833px" href="#">FAQS</a>
    <a style="left:918px" href="#">BLOG</a>
    <a style="left:1000px" href="#">CONTACT</a>
  </nav>
  <div class="rule" style="top:175px"></div>
  <div class="copyright">Copyright © 2021 All Rights Reserved</div>
</footer>
</body>
</html>
```